QP Fiduciary Website Redesign Contest

We want to refresh our website to be more insitutional, professional for an international audience. We have designed a new logo for this purpose and that has been attached. A full brand brief and positioning statement has also been attached. Please read through all the documents carefully before designing. The old website is found here: https://qp-fiduciary.example/

Target Market(s)

Actuaries and associated businesses internationally

Industry/Entity Type

professional services - actuaries

Number of Pages Required

3 page

Font styles to use
Sans Serif

Colors
0054AA
0677BA
7BADD7
CADEEF
E8F1F8
0094D4
00A9DD
6FCCEA
C7EBF8
E9F6FB
F0912C
F2A743
F7CA91
FBE8D2
FDF5EE
EE7325
F08F49
F5BC92
FAE3D3
FDF4ED
EB3D1F
EC4F4E
F09395
F8D3D4
FCEDEE

Requirements
Must have
• blues and greens to match the logo color, complimentary colors, navigation
Nice to have
• old site: https://qp-fiduciary.example/

```html
<!DOCTYPE html>
<html lang="en">
<head>
<meta charset="utf-8">
<title>QP Fiduciary — Actuarial Software</title>
<link href="https://fonts.googleapis.com/css2?family=Orbitron:wght@400;800&family=Poppins:wght@300;400;500;600;700&display=swap" rel="stylesheet">
<style>
:root{
  --blue:#0054AA;
  --blue-mid:#0677BA;
  --sky:#00A9DD;
  --ice:#E8F1F8;
  --band:#EEF1FC;
  --teal:#0E8E86;
  --teal-light:#E3F4F2;
  --orange:#EE7325;
  --orange-soft:#F08F49;
  --navy:#0B1633;
  --ink:#14182A;
  --grey:#4A4F60;
  --line:#E4E7EF;
  --white:#FFFFFF;
}
*{box-sizing:border-box;margin:0;padding:0}
html,body{width:1200px;height:4454px;overflow:hidden}
body{font-family:"Poppins",sans-serif;color:var(--ink);background:var(--white);position:relative}
.abs{position:absolute}
.logo{display:flex;align-items:center;gap:10px;font-family:"Poppins",sans-serif;font-weight:600;letter-spacing:1px}
.logo-dot{width:16px;height:16px;border-radius:50%;background:var(--orange)}

/* header */
.site-header{position:absolute;left:0;top:0;width:1200px;height:75px;background:var(--white)}
.site-header .logo{position:absolute;left:69px;top:22px;font-size:26px;color:var(--navy)}
.main-nav{position:absolute;left:391px;top:29px;display:flex;gap:31px;font-size:13px;color:var(--ink)}
.main-nav .active{color:var(--blue-mid)}
.btn-orange{background:var(--orange);color:var(--white);border-radius:22px;font-size:13px;font-weight:500;display:flex;align-items:center;justify-content:center;gap:12px}
.site-header .btn-orange{position:absolute;left:875px;top:20px;width:253px;height:38px}

/* hero */
.hero{position:absolute;left:0;top:75px;width:1200px;height:544px;background:linear-gradient(100deg,#0F1727 0%,#1D2A40 40%,#5B6C82 75%,#A9B5C3 100%)}
.hero-shade{position:absolute;inset:0;background:linear-gradient(90deg,rgba(8,12,24,.85),rgba(8,12,24,.3) 60%,rgba(8,12,24,0))}
.hero h1{position:absolute;left:69px;top:120px;font-family:"Orbitron",sans-serif;font-weight:400;font-size:31px;line-height:43px;color:var(--white);letter-spacing:.5px}
.hero h1 b{font-weight:800}
.hero p{position:absolute;left:71px;top:300px;width:480px;font-size:13.5px;line-height:22px;color:#E6E9F0}
.hero .btn-orange{position:absolute;left:71px;top:375px;width:323px;height:43px;font-size:14px}
.arrow-dot{width:28px;height:28px;border-radius:50%;background:var(--white);display:flex;align-items:center;justify-content:center}

/* shared */
.pill{position:absolute;height:30px;border:1px solid #7FC7BE;background:var(--teal-light);color:var(--teal);border-radius:16px;font-size:12px;display:flex;align-items:center;justify-content:center;padding:0 20px}
.sec-title{position:absolute;left:0;width:1200px;text-align:center;font-size:38px;font-weight:400;color:var(--ink)}
.sec-title b{font-weight:700}
.sec-sub{position:absolute;left:0;width:1200px;text-align:center;font-size:12.5px;line-height:22px;color:var(--grey)}
.btn-teal{position:absolute;height:45px;background:var(--teal);color:var(--white);border-radius:24px;font-size:12.5px;font-weight:500;display:flex;align-items:center;justify-content:space-between;padding:0 6px 0 16px}
.btn-teal .arrow-dot{width:36px;height:36px}

/* overview cards */
.feature-card{position:absolute;top:903px;width:209px;height:164px;background:var(--white);border-radius:14px;box-shadow:0 6px 22px rgba(20,30,60,.10);padding:52px 16px 0}
.feature-card h3{font-size:15px;font-weight:500;line-height:20px;margin-bottom:6px}
.feature-card p{font-size:11.5px;line-height:18px;color:var(--grey)}
.feature-icon{position:absolute;left:16px;top:-30px;width:62px;height:62px;border-radius:12px;display:flex;align-items:center;justify-content:center}

/* solutions */
.band{position:absolute;left:-200px;width:1600px;background:var(--band)}
.solution-card{position:absolute;background:var(--white);border-radius:10px;box-shadow:0 6px 22px rgba(20,30,60,.10);padding:70px 15px 0}
.solution-card h3{font-size:14px;font-weight:500;margin-bottom:6px}
.solution-card p{font-size:11.5px;line-height:18px;color:var(--grey)}
.corner{position:absolute;right:8px;bottom:8px;width:24px;height:24px;border-radius:5px;background:var(--teal);display:flex;align-items:center;justify-content:center}
.sol-icon{position:absolute;left:15px;top:14px;width:60px;height:54px}

/* characteristics */
.trait-label{position:absolute;font-size:14px;line-height:21px;color:var(--ink)}
.trait-icon{position:absolute;width:70px;height:70px;border-radius:50%;display:flex;align-items:center;justify-content:center}
.hub{position:absolute;left:453px;top:2104px;width:294px;height:139px;border-radius:70px;background:var(--white);box-shadow:0 8px 30px rgba(20,30,60,.12);display:flex;align-items:center;justify-content:center}
.hub .logo{font-size:24px;color:var(--navy)}

/* insights */
.post{position:absolute;background:var(--white);border-radius:6px;box-shadow:0 4px 18px rgba(20,30,60,.10)}
.post-img{position:absolute;border-radius:6px}
.meta{display:flex;gap:14px;font-size:9.5px;font-weight:500;color:var(--ink);align-items:center}
.meta i{display:inline-block;width:11px;height:11px;border-radius:2px;background:var(--blue-mid);margin-right:6px;vertical-align:-1px}
.meta i.person{border-radius:50%}
.post h4{font-weight:500;color:var(--ink)}
.read-more{display:inline-flex;align-items:center;justify-content:center;border:1px solid var(--orange-soft);color:var(--orange);border-radius:4px;font-weight:500}
.small-post .body{position:absolute;left:201px;top:18px;width:240px}
.small-post h4{font-size:13.5px;line-height:21px;margin-top:8px}
.small-post p{font-size:10px;line-height:16px;color:var(--grey);margin-top:4px}
.small-post .read-more{font-size:9.5px;width:86px;height:26px;margin-top:8px}

/* cta */
.cta{position:absolute;left:142px;top:3515px;width:916px;height:372px;border-radius:36px 24px 90px 36px;overflow:hidden;background:linear-gradient(100deg,#0E9A88 0%,#0A8A8C 40%,#0677BA 75%)}
.cta-photo{position:absolute;left:508px;top:0;width:408px;height:372px;border-radius:50px 0 0 0;background:linear-gradient(135deg,#EEF1F4,#B9C3CC 55%,#5F6D7B)}
.cta .pill{left:45px;top:72px;background:transparent;border-color:rgba(255,255,255,.85);color:var(--white)}
.cta h2{position:absolute;left:45px;top:128px;font-size:37px;line-height:43px;font-weight:400;color:var(--white)}
.cta h2 b{font-weight:700}
.cta p{position:absolute;left:45px;top:210px;width:440px;font-size:12px;line-height:21px;color:#EAF6F6}
.cta .btn-cta{position:absolute;left:45px;top:264px;width:306px;height:44px;border-radius:24px;background:var(--white);color:var(--navy);font-size:12px;font-weight:500;display:flex;align-items:center;justify-content:space-between;padding:0 6px 0 16px}

/* footer */
.site-footer{position:absolute;left:0;top:3977px;width:1200px;height:477px}
.site-footer .logo{position:absolute;left:142px;top:188px;font-size:24px;color:var(--white)}
.foot-about{position:absolute;left:142px;top:246px;width:225px;font-size:11.5px;line-height:19px;color:#D6DBE6}
.foot-col{position:absolute;top:182px;color:var(--white)}
.foot-col h5{font-size:17px;font-weight:500;margin-bottom:10px}
.foot-col li{list-style:none;font-size:13px;line-height:28px;color:#D6DBE6}
.contact-item{display:flex;gap:10px;font-size:12.5px;line-height:20px;color:#D6DBE6;margin-bottom:14px}
.social{display:flex;align-items:center;gap:12px;font-size:13px;color:#D6DBE6;margin-bottom:13px}
.social span{width:29px;height:29px;border-radius:50%;border:1px solid #C8CFDC}
.social span.on{background:var(--teal);border-color:var(--teal)}
.foot-rule{position:absolute;left:142px;top:415px;width:916px;height:1px;background:#2B3656}
.foot-bottom{position:absolute;left:142px;top:440px;width:916px;display:flex;justify-content:space-between;font-size:12px;color:#D6DBE6}
</style>
</head>
<body>

<header class="site-header">
  <div class="logo"><span class="logo-dot"></span>QP FIDUCIARY</div>
  <nav class="main-nav"><span class="active">Home</span><span>Platform</span><span>Solutions</span><span>Insights</span><span>Company</span><span>Contact</span></nav>
  <div class="btn-orange">Request a Technical Walkthrough</div>
</header>

<section class="hero">
  <div class="abs" role="img" aria-label="Photo of hands working on a tablet showing financial charts" style="inset:0"></div>
  <div class="hero-shade"></div>
  <h1>ACTUARIAL SOFTWARE<br>FOR <b>STRUCTURED,</b><br><b>AUDITABLE FINANCIAL</b><br><b>ANALYSIS.</b></h1>
  <p><b>QP Fiduciary</b> develops software that translates established actuarial methodologies into disciplined, decision-ready tools.</p>
  <div class="btn-orange">Request A Technical Walkthrough <span class="arrow-dot"><svg width="14" height="14" viewBox="0 0 14 14"><path d="M2 7h10M8 3l4 4-4 4" stroke="#EE7325" stroke-width="1.8" fill="none"/></svg></span></div>
</section>

<!-- platform overview -->
<div class="pill" style="left:510px;top:714px;width:180px">PLATFORM OVERVIEW</div>
<h2 class="sec-title" style="top:748px">Built For Actuarial <b>Excellence</b></h2>
<p class="sec-sub" style="top:804px">Our Platform Delivers Structured Workflows, Transparent Assumptions, And Complete Auditability<br>—Enabling Confident, Governance-Ready Financial Analysis.</p>

<div class="feature-card" style="left:142px">
  <div class="feature-icon" style="background:var(--blue-mid)"><svg width="34" height="30" viewBox="0 0 34 30" fill="none" stroke="#fff" stroke-width="2"><rect x="2" y="2" width="30" height="18" rx="2"/><path d="M10 26h14M17 20v6"/></svg></div>
  <h3>Structured Workflows</h3>
  <p>Disciplined Processes That Guide Analysis From Input To Output With Clear, Repeatable Steps.</p>
</div>
<div class="feature-card" style="left:377px">
  <div class="feature-icon" style="background:var(--orange)"><svg width="32" height="32" viewBox="0 0 32 32" fill="none" stroke="#fff" stroke-width="2"><circle cx="16" cy="16" r="12"/><path d="M16 4v12h12"/></svg></div>
  <h3>Transparency<br>of Assumptions</h3>
  <p>Every Assumption Is Documented, Visible, And Traceable Throughout.</p>
</div>
<div class="feature-card" style="left:614px">
  <div class="feature-icon" style="background:var(--blue)"><svg width="30" height="34" viewBox="0 0 30 34" fill="none" stroke="#fff" stroke-width="2"><rect x="3" y="2" width="22" height="28" rx="2"/><path d="M9 18l4 4 8-8"/></svg></div>
  <h3>Auditability</h3>
  <p>Complete Audit Trails With Version Control And Comprehensive Documentation At Every Step.</p>
</div>
<div class="feature-card" style="left:849px">
  <div class="feature-icon" style="background:var(--teal)"><svg width="34" height="32" viewBox="0 0 34 32" fill="none" stroke="#fff" stroke-width="2"><path d="M3 14L17 3l14 11M7 12v16h20V12"/><path d="M13 28v-8h8v8"/></svg></div>
  <h3>Governance</h3>
  <p>Built-In Controls And Approval Workflows That Ensure Regulatory Compliance.</p>
</div>

<!-- solutions -->
<div class="band" style="top:1155px;height:626px;border-radius:50% 50% 50% 50% / 18% 18% 18% 18%"></div>
<div class="pill" style="left:142px;top:1350px;width:148px">OUR SOLUTIONS</div>
<h2 class="abs" style="left:142px;top:1386px;font-size:38px;line-height:43px;font-weight:400">Comprehensive<br><b>Actuarial Suite</b></h2>
<p class="abs" style="left:142px;top:1480px;width:380px;font-size:12.5px;line-height:22px;color:var(--grey)">Three Integrated Solution Areas Designed To Address The Full Spectrum Of Actuarial Analysis Needs.</p>
<div class="btn-teal" style="left:142px;top:1546px;width:304px">REQUEST A TECHNICAL WALKTHROUGH <span class="arrow-dot"><svg width="16" height="14" viewBox="0 0 16 14"><path d="M1 7h13M9 2l5 5-5 5" stroke="#0B1633" stroke-width="1.8" fill="none"/></svg></span></div>

<div class="abs" style="left:792px;top:1305px;width:20px;height:26px;background:var(--teal)"></div>
<div class="solution-card" style="left:546px;top:1267px;width:246px;height:222px">
  <svg class="sol-icon" viewBox="0 0 60 54" fill="none" stroke="#0054AA" stroke-width="2.4"><rect x="10" y="4" width="28" height="36" rx="3"/><path d="M16 14h16M16 22h16M16 30h10"/><circle cx="44" cy="40" r="9"/></svg>
  <h3>Reserving &amp; Valuation</h3>
  <p>Comprehensive Reserve Calculations And Liability Valuations With Transparent Methodology Documentation And Multi-Standard Support.</p>
  <div class="corner"><svg width="12" height="12" viewBox="0 0 12 12"><path d="M2 10L10 2M4 2h6v6" stroke="#fff" stroke-width="1.6" fill="none"/></svg></div>
</div>
<div class="solution-card" style="left:811px;top:1267px;width:245px;height:222px">
  <svg class="sol-icon" viewBox="0 0 60 54" fill="none" stroke="#0054AA" stroke-width="2.4"><path d="M8 8h22l22 22-18 18L8 26z"/><circle cx="18" cy="18" r="4"/></svg>
  <h3>Pricing</h3>
  <p>Sophisticated Pricing Models That Balance Profitability Targets With Competitive Positioning And Regulatory Requirements.</p>
  <div class="corner"><svg width="12" height="12" viewBox="0 0 12 12"><path d="M2 10L10 2M4 2h6v6" stroke="#fff" stroke-width="1.6" fill="none"/></svg></div>
</div>
<div class="solution-card" style="left:686px;top:1508px;width:248px;height:200px">
  <svg class="sol-icon" viewBox="0 0 60 54" fill="none" stroke="#0054AA" stroke-width="2.4"><circle cx="34" cy="20" r="12"/><circle cx="34" cy="20" r="4"/><path d="M4 44l10-18 10 18z"/></svg>
  <h3>Enterprise Risk Management</h3>
  <p>Holistic Risk Assessment And Capital Modeling That Integrates Across Business Units And Regulatory Frameworks.</p>
  <div class="corner"><svg width="12" height="12" viewBox="0 0 12 12"><path d="M2 10L10 2M4 2h6v6" stroke="#fff" stroke-width="1.6" fill="none"/></svg></div>
</div>

<!-- characteristics -->
<div class="pill" style="left:525px;top:1872px;width:150px">WHY CHOOSE US</div>
<h2 class="sec-title" style="top:1906px">Platform <b>Characteristics</b></h2>
<p class="sec-sub" style="top:1962px">Key Attributes That Set Our Platform Apart In Delivering Reliable, Governance-Ready<br>Actuarial Analysis.</p>

<svg class="abs" style="left:0;top:2030px" width="1200" height="290" fill="none" stroke="#D5DAE6" stroke-width="1.2">
  <path d="M450 40L501 78M750 40L700 78M450 245L501 213M750 245L700 213"/>
  <g stroke="#0677BA" stroke-width="2" fill="#fff"><circle cx="501" cy="78" r="5"/><circle cx="700" cy="78" r="5"/><circle cx="501" cy="213" r="5"/><circle cx="700" cy="213" r="5"/></g>
</svg>
<div class="hub"><div class="logo"><span class="logo-dot"></span>QP FIDUCIARY</div></div>

<p class="trait-label" style="left:280px;top:2050px;text-align:right;width:85px">Structured Workflows</p>
<div class="trait-icon" style="left:380px;top:2035px;background:var(--blue)"><svg width="34" height="34" viewBox="0 0 34 34" fill="none" stroke="#fff" stroke-width="2.2"><circle cx="17" cy="9" r="5"/><path d="M17 14v6M7 26v-6h20v6"/><circle cx="7" cy="29" r="3"/><circle cx="17" cy="29" r="3"/><circle cx="27" cy="29" r="3"/></svg></div>
<div class="trait-icon" style="left:748px;top:2035px;background:var(--teal)"><svg width="34" height="34" viewBox="0 0 34 34" fill="none" stroke="#fff" stroke-width="2.2"><path d="M5 29h24M9 25V17M15 25V11M21 25V15M27 25V7"/></svg></div>
<p class="trait-label" style="left:835px;top:2050px">Comparative<br>Analysis Capability</p>

<p class="trait-label" style="left:220px;top:2253px;text-align:right;width:150px">Multi-Jurisdictional<br>Review Support</p>
<div class="trait-icon" style="left:380px;top:2240px;background:var(--teal)"><svg width="34" height="34" viewBox="0 0 34 34" fill="none" stroke="#fff" stroke-width="2.2"><circle cx="17" cy="14" r="9"/><path d="M8 14h18M17 5c4 4 4 14 0 18M17 5c-4 4-4 14 0 18M6 30h22"/></svg></div>
<div class="trait-icon" style="left:748px;top:2240px;background:var(--blue)"><svg width="34" height="34" viewBox="0 0 34 34" fill="none" stroke="#fff" stroke-width="2.2"><path d="M4 17s5-8 13-8 13 8 13 8-5 8-13 8S4 17 4 17z"/><circle cx="17" cy="17" r="4"/></svg></div>
<p class="trait-label" style="left:832px;top:2253px">Transparent<br>Assumptions</p>

<div class="btn-teal" style="left:450px;top:2357px;width:306px">REQUEST A TECHNICAL WALKTHROUGH <span class="arrow-dot"><svg width="16" height="14" viewBox="0 0 16 14"><path d="M1 7h13M9 2l5 5-5 5" stroke="#0B1633" stroke-width="1.8" fill="none"/></svg></span></div>

<!-- insights -->
<div class="band" style="top:2490px;height:900px;border-radius:50% 50% 0 0 / 10% 10% 0 0;background:linear-gradient(180deg,var(--band) 0%,var(--band) 70%,#fff 100%)"></div>
<div class="pill" style="left:525px;top:2559px;width:106px">INSIGHTS</div>
<h2 class="sec-title" style="top:2593px">Insights &amp; Thought <b>Leadership</b></h2>
<p class="sec-sub" style="top:2648px">Key Attributes That Set Our Platform Apart In Delivering Reliable, Governance-Ready<br>Actuarial Analysis.</p>

<article class="post" style="left:142px;top:2718px;width:448px;height:539px">
  <div class="post-img" role="img" aria-label="Photo of two professionals in discussion beside a glowing light bulb graphic" style="left:14px;top:12px;width:421px;height:291px;background:linear-gradient(135deg,#0B2A5A,#1F5FA8 50%,#6FB6E8)"></div>
  <div class="meta abs" style="left:16px;top:330px"><span><i></i>24 JUL 2025</span><span><i class="person"></i>AUTHOR:&nbsp; Simon Keller</span></div>
  <h4 class="abs" style="left:16px;top:356px;font-size:17px">RBC (Risk-Based Capital)</h4>
  <p class="abs" style="left:16px;top:392px;width:410px;font-size:11.5px;line-height:22px;color:var(--grey)">Bayside, 24 July 2025 – <u>QP FIDUCIARY</u> is an independent actuarial consulting firm headquartered in Bayside, Florida, with operations in Port Alder, Westland, and a presence in Northvale under HALVERN ACTUARY LLP. We specialize...</p>
  <span class="read-more abs" style="left:16px;top:482px;width:108px;height:38px;font-size:11.5px">READ MORE</span>
</article>

<article class="post small-post" style="left:609px;top:2718px;width:449px;height:169px">
  <div class="post-img" role="img" aria-label="Photo of a financial chart with rising lines" style="left:12px;top:12px;width:169px;height:145px;background:linear-gradient(135deg,#E9EEF5,#9AA8BB 50%,#C45A3A)"></div>
  <div class="body"><div class="meta"><span><i></i>13 JAN 2026</span><span><i class="person"></i>AUTHOR: ADRIEN SOLO</span></div>
  <h4>Evolution into Technology-Led Actuarial Platform</h4>
  <p>Bayside, January 12, 2026 – QP FIDUCIARY is thrilled to share...</p>
  <span class="read-more">READ MORE</span></div>
</article>
<article class="post small-post" style="left:609px;top:2905px;width:449px;height:169px">
  <div class="post-img" role="img" aria-label="Illustration of a city skyline with financial literacy and inclusion theme" style="left:12px;top:12px;width:169px;height:145px;background:linear-gradient(160deg,#2E7F7A,#6BA35A 50%,#D8B24A)"></div>
  <div class="body"><div class="meta"><span><i></i>18 JUN 2025</span><span><i class="person"></i>AUTHOR: REMI DALTON</span></div>
  <h4>Financial Literacy and Inclusion: Leveraging actuarial expertise to improve financial understanding...</h4>
  <span class="read-more">READ MORE</span></div>
</article>
<article class="post small-post" style="left:609px;top:3090px;width:449px;height:169px">
  <div class="post-img" role="img" aria-label="Photo of a conference audience facing a digital innovation display" style="left:12px;top:12px;width:169px;height:145px;background:linear-gradient(180deg,#1B3A5C,#3F78A6 45%,#1A2230)"></div>
  <div class="body"><div class="meta"><span><i></i>27 MAR 2025</span><span><i class="person"></i>AUTHOR: Marion</span></div>
  <h4>Innovation and Regulation in Insurance Insights from the Regional Insurance Industry Innovation Forum</h4>
  <span class="read-more">READ MORE</span></div>
</article>

<div class="btn-teal" style="left:508px;top:3302px;width:182px">VIEW ALL ARTICLES <span class="arrow-dot"><svg width="16" height="14" viewBox="0 0 16 14"><path d="M1 7h13M9 2l5 5-5 5" stroke="#0B1633" stroke-width="1.8" fill="none"/></svg></span></div>

<!-- call to action -->
<section class="cta">
  <div class="cta-photo" role="img" aria-label="Photo of a person reviewing bar charts on a laptop and printed reports"></div>
  <div class="pill">SCHEDULE A DEMO</div>
  <h2>Ready To Transform<br>Your <b>Actuarial Practice?</b></h2>
  <p>Discover How QP Fiduciary's Platform Can Bring Structure, Transparency, And Confidence To Your Financial Analysis Workflows.</p>
  <div class="btn-cta">REQUEST A TECHNICAL WALKTHROUGH <span class="arrow-dot" style="width:36px;height:36px;background:var(--teal)"><svg width="16" height="14" viewBox="0 0 16 14"><path d="M1 7h13M9 2l5 5-5 5" stroke="#fff" stroke-width="1.8" fill="none"/></svg></span></div>
</section>

<!-- footer -->
<footer class="site-footer">
  <svg class="abs" style="left:0;top:0" width="1200" height="477" viewBox="0 0 1200 477" preserveAspectRatio="none">
    <path d="M0 140C300 60 700 20 1200 0V477H0Z" fill="#EE7325"/>
    <path d="M0 172C320 95 720 70 1200 80V477H0Z" fill="#0B1633"/>
  </svg>
  <div class="logo"><span class="logo-dot"></span>QP FIDUCIARY</div>
  <p class="foot-about">Common Approach To Service Delivery Can Be Described Within A Cycle That Involves Defining The Problem, Designing A Solution And Monitoring The Results.</p>
  <div class="foot-col" style="left:469px"><h5>Quick Links</h5><ul><li>Company</li><li>Platform</li><li>Solutions</li><li>Insights</li><li>Contact</li></ul></div>
  <div class="foot-col" style="left:664px;width:230px"><h5>Contact Details</h5>
    <div class="contact-item"><svg width="12" height="16" viewBox="0 0 12 16"><path d="M6 15s5-6 5-9A5 5 0 0 0 1 6c0 3 5 9 5 9z" fill="#fff"/><circle cx="6" cy="6" r="2" fill="#0B1633"/></svg><span>1480 Harbour View Blvd, Suite 210<br>Bayside, FL 33100</span></div>
    <div class="contact-item"><svg width="13" height="13" viewBox="0 0 13 13"><path d="M2 1l3 0 1 3-2 1a7 7 0 0 0 4 4l1-2 3 1v3c-6 0-10-4-10-10z" fill="#fff"/></svg><span>Phone<br>+1(555)014-2290</span></div>
    <div class="contact-item"><svg width="13" height="11" viewBox="0 0 13 11"><rect x="0.5" y="0.5" width="12" height="10" fill="#fff"/><path d="M1 1l5.5 5L12 1" stroke="#0B1633" fill="none"/></svg><span>Email<br>contact@qp-fiduciary.example</span></div>
  </div>
  <div class="foot-col" style="left:942px"><h5>Social Media</h5>
    <div class="social"><span class="on"></span>Social Feed</div>
    <div class="social"><span></span>Video Channel</div>
    <div class="social"><span></span>Pro Network</div>
    <div class="social"><span></span>Photo Stream</div>
  </div>
  <div class="foot-rule"></div>
  <div class="foot-bottom"><span>© 2026 QP Fiduciary All Rights Reserved.</span><span>Price Policy &nbsp;Terms And Conditions</span></div>
</footer>

</body>
</html>
```